Request for Business Card Design

Hi. My name is Marlene, I am looking for a new business card design for my company, Quarrow Signal Instruments, LLC. I really like the design you did for Tarsel Venture and was hoping you could do something similar using our full logo and our mark. I am also open to any raised texture design using our mark. I have attached our full logo, which would need to be somewhere on the card, as well as the mark in both outline and full form, as well as our brand colors / guide. The card does not have to be white, as long as our logo and mark appear. I actually like darker colored business cards more, but am open to all options. If you are interested in working with me, please let me know. We would also take the business card design into letterhead design if you can do that.

```html
<!DOCTYPE html>
<html lang="en">
<head>
<meta charset="utf-8">
<title>Quarrow Signal Instruments — Business Card</title>
<link href="https://fonts.googleapis.com/css2?family=Open+Sans:wght@400;600;800&display=swap" rel="stylesheet">
<style>
  :root {
    --stage: #3a3a3c;
    --card: #151516;
    --card-edge: #1d1d1f;
    --pattern-light: #262628;
    --pattern-dark: #0c0c0d;
    --accent: #1297c9;
    --ink: #ffffff;
    --ink-soft: #8a8a8e;
  }
  * { margin: 0; padding: 0; box-sizing: border-box; }
  html, body { width: 1200px; height: 689px; overflow: hidden; }
  body {
    background: var(--stage);
    font-family: "Open Sans", Arial, sans-serif;
    color: var(--ink);
    position: relative;
  }
  .card {
    position: absolute;
    top: 190px;
    width: 540px;
    height: 309px;
    border-radius: 18px;
    background: var(--card);
    box-shadow: 0 14px 34px rgba(0,0,0,.45);
    overflow: hidden;
  }
  .card--back { left: 50px; }
  .card--front { left: 610px; }

  /* back */
  .texture-field {
    position: absolute; inset: 0;
    background: linear-gradient(120deg, var(--pattern-light) 0%, var(--pattern-dark) 55%, var(--pattern-light) 100%);
  }
  .lockup {
    position: absolute;
    display: flex; align-items: center; gap: 14px;
  }
  .lockup__dot {
    width: 46px; height: 46px; border-radius: 50%;
    background: var(--accent); flex: none;
  }
  .lockup__name {
    font-weight: 800; letter-spacing: 3px; line-height: 1;
  }
  .lockup__tagline {
    font-weight: 600; letter-spacing: 1.2px; text-transform: uppercase; margin-top: 4px;
  }
  .card--back .lockup { left: 50%; top: 50%; transform: translate(-50%, -50%); }
  .card--back .lockup__name { font-size: 38px; color: var(--ink-soft); }
  .card--back .lockup__tagline { font-size: 10.5px; color: var(--ink-soft); }

  /* front */
  .accent-tab {
    position: absolute; top: 22px; right: 0;
    width: 14px; height: 40px; background: var(--accent);
  }
  .person { position: absolute; top: 22px; right: 30px; text-align: right; }
  .person__name { font-size: 22px; font-weight: 800; color: var(--accent); letter-spacing: .5px; line-height: 1.1; }
  .person__role { font-size: 13px; font-weight: 400; }
  .card--front .lockup { left: 34px; top: 98px; }
  .card--front .lockup__name { font-size: 40px; color: var(--ink); }
  .card--front .lockup__tagline { font-size: 10.5px; color: var(--ink); }
  .address { position: absolute; left: 34px; top: 190px; font-size: 13px; line-height: 1.35; }
  .contacts { position: absolute; left: 34px; top: 236px; list-style: none; font-size: 13px; line-height: 1.45; }
  .contacts li { display: flex; align-items: center; gap: 8px; }
  .contacts svg { width: 11px; height: 11px; fill: var(--accent); flex: none; }
</style>
</head>
<body>
  <section class="card card--back">
    <div class="texture-field" role="img" aria-label="Raised tone-on-tone texture of the brand mark repeated across the card"></div>
    <div class="lockup">
      <span class="lockup__dot"></span>
      <div>
        <div class="lockup__name">QUARROW</div>
        <div class="lockup__tagline">Signal Instruments</div>
      </div>
    </div>
  </section>

  <section class="card card--front">
    <span class="accent-tab"></span>
    <div class="person">
      <div class="person__name">OWEN HARTLEY</div>
      <div class="person__role">Managing Director</div>
    </div>
    <div class="lockup">
      <span class="lockup__dot"></span>
      <div>
        <div class="lockup__name">QUARROW</div>
        <div class="lockup__tagline">Signal Instruments</div>
      </div>
    </div>
    <p class="address">Your address, City<br>State, Zip 1234</p>
    <ul class="contacts">
      <li><svg viewBox="0 0 16 16"><path d="M3.5 1.5l3 3-2 2c1 2 3 4 5 5l2-2 3 3-2 2.5C7 14.5 1.5 9 1 3.5z"/></svg>123 456 789</li>
      <li><svg viewBox="0 0 16 16"><path d="M1 3h14v10H1zM1 3l7 6 7-6" stroke="#151516" stroke-width="1.2"/></svg>info@yourgmail.com</li>
      <li><svg viewBox="0 0 16 16"><circle cx="8" cy="8" r="7"/><path d="M1 8h14M8 1c-3 4-3 10 0 14M8 1c3 4 3 10 0 14" stroke="#151516" stroke-width="1" fill="none"/></svg>www.yourwebsite.com</li>
    </ul>
  </section>
</body>
</html>
```